Profesional personal website needs design and business card

I need a business card with my professional name as a logo "Dorian Vitality" for my business. I am a Wellness Coach, consultant and trainer. So it should be professional, wellness oriented and modern.

Target Market(s)

Private clients, governments, corporations. Luxury and high market.

Industry/Entity Type

Health And Wellness

Contact Information for Business Card

Dorian Vitality should be the logo

Colors

Designer to choose colors to be used in the design.

Requirements
Must have
• Dorian Vitality
• Name: Tomás Lirandel
• Wellness Coach, Consultant & Trainer.
• Website: www.dorianvitality-example.com
• Phone:
• Spain (+34) 612 480 317
• (USA) +1 (555) 610 4829
Nice to have
• The most important is the design of "Dorian Vitality", as this is going to be my personal brand logo. It should be professional, wellness, high end and actual.
Should not have
• no golds, no baroque style..

```html
<!DOCTYPE html>
<html lang="en">
<head>
<meta charset="UTF-8">
<title>Dorian Vitality – Business Card</title>
<link href="https://fonts.googleapis.com/css2?family=Lato:wght@400;700&display=swap" rel="stylesheet">
<style>
  :root {
    --brand-blue: #01729b;
    --ink: #222222;
    --ink-soft: #4a4f55;
    --paper: #ffffff;
    --page: #ffffff;
    --shadow: rgba(0, 0, 0, 0.22);
  }
  * { box-sizing: border-box; margin: 0; padding: 0; }
  html, body {
    width: 1200px;
    height: 1200px;
    overflow: hidden;
    background: var(--page);
    font-family: "Lato", sans-serif;
  }
  .canvas { position: relative; width: 1200px; height: 1200px; }

  .card {
    position: absolute;
    left: 180px;
    width: 840px;
    height: 477px;
    box-shadow: 4px 5px 7px var(--shadow);
  }
  .card--front { top: 84px; background: var(--paper); }
  .card--back { top: 640px; background: var(--brand-blue); }

  .wordmark {
    position: absolute;
    display: flex;
    align-items: center;
    gap: 14px;
    font-weight: 700;
    white-space: nowrap;
    transform: translate(-50%, -50%);
  }
  .wordmark__square { display: block; flex: none; }
  .card--front .wordmark {
    left: 232px; top: 236px;
    font-size: 44px;
    color: var(--brand-blue);
  }
  .card--front .wordmark__square { width: 22px; height: 22px; background: var(--brand-blue); }
  .card--back .wordmark {
    left: 420px; top: 240px;
    font-size: 64px;
    color: var(--paper);
  }
  .card--back .wordmark__square { width: 30px; height: 30px; background: var(--paper); }

  .divider {
    position: absolute;
    left: 418px; top: 154px;
    width: 3px; height: 164px;
    background: var(--brand-blue);
  }

  .identity { position: absolute; left: 460px; top: 152px; }
  .identity__name {
    font-size: 37px;
    font-weight: 700;
    color: var(--brand-blue);
    line-height: 1.1;
    letter-spacing: -0.2px;
  }
  .identity__role {
    margin-top: 4px;
    font-size: 19px;
    color: var(--ink-soft);
  }

  .contacts { position: absolute; left: 460px; top: 236px; list-style: none; }
  .contacts__item {
    display: flex;
    align-items: center;
    gap: 9px;
    height: 29.5px;
    font-size: 19.5px;
    color: var(--ink);
  }
  .contacts__item svg { width: 18px; height: 18px; flex: none; }
  .contacts__region { color: var(--brand-blue); }

  .back-url {
    position: absolute;
    left: 0; right: 0; top: 422px;
    text-align: center;
    font-size: 19px;
    color: var(--paper);
  }
</style>
</head>
<body>
<main class="canvas">
  <section class="card card--front">
    <div class="wordmark"><span class="wordmark__square"></span>Dorian Vitality</div>
    <div class="divider"></div>
    <div class="identity">
      <h1 class="identity__name">Tomás Lirandel</h1>
      <p class="identity__role">Wellness Coach, Consultant &amp; Trainer</p>
    </div>
    <ul class="contacts">
      <li class="contacts__item">
        <svg viewBox="0 0 24 24" aria-hidden="true"><path fill="#01729b" d="M6.6 2.5l3 3.6c.4.5.4 1.2 0 1.7L8 9.6c1.2 2.6 3.7 5.1 6.4 6.4l1.8-1.6c.5-.4 1.2-.4 1.7 0l3.6 3c.5.4.6 1.2.1 1.7l-1.8 2c-.7.7-1.8 1-2.8.6C10.2 19.5 4.5 13.8 2.3 7c-.3-1 0-2.1.7-2.8l1.9-1.8c.5-.5 1.3-.4 1.7.1z"/></svg>
        <span>(+34) 612 480 317 <span class="contacts__region">Spain</span></span>
      </li>
      <li class="contacts__item">
        <svg viewBox="0 0 24 24" aria-hidden="true"><rect x="7" y="4" width="10" height="18" rx="2" fill="#01729b"/><rect x="9" y="6.5" width="6" height="11" fill="#ffffff"/><circle cx="12" cy="19.8" r="0.9" fill="#ffffff"/></svg>
        <span>+1 (555) 610 4829 <span class="contacts__region">(USA)</span></span>
      </li>
      <li class="contacts__item">
        <svg viewBox="0 0 24 24" aria-hidden="true"><circle cx="12" cy="12" r="9" fill="none" stroke="#01729b" stroke-width="2"/><ellipse cx="12" cy="12" rx="4" ry="9" fill="none" stroke="#01729b" stroke-width="1.6"/><path d="M3 12h18" stroke="#01729b" stroke-width="1.6"/></svg>
        <span>www.dorianvitality-example.com</span>
      </li>
    </ul>
  </section>

  <section class="card card--back">
    <div class="wordmark"><span class="wordmark__square"></span>Dorian Vitality</div>
    <p class="back-url">www.dorianvitality-example.com</p>
  </section>
</main>
</body>
</html>
```